Business Card Design

Need a new business card to represent our legal vertical focus. attached is an example of our old business card and newest logo. we would like the card to also identify "Legal Tech" as a tag line of business.

Our new address is
4817 Marlowe Hatchfield Rd.
Suite 518
Cincinnati, OH 45917

we no longer have a fax number.

Target Market(s)

Tech Consulting for Law Firms

Industry/Entity Type

Legal

Contact Information for Business Card

should use logo and colors. we are a b2b company

Font styles to use
Other font styles liked:
• tahoma

Requirements
Must have
• all print should be in lower case just as shown in photos. tag line should not
Should not have
• pinstripes or drop shadows

```html
<!DOCTYPE html>
<html lang="en">
<head>
<meta charset="utf-8">
<title>Threadline Legal Tech — Business Card</title>
<link rel="stylesheet" href="https://fonts.googleapis.com/css2?family=PT+Sans:wght@400;700&display=swap">
<style>
  :root {
    --page: #ebe8e3;
    --card-white: #ffffff;
    --card-black: #0b0b0b;
    --brand-blue: #2c3f8e;
    --panel-blue: #2b3d88;
    --tag-grey: #6d6d6d;
    --url-grey: #6a6a6a;
    --text-light: #ffffff;
  }
  * { box-sizing: border-box; margin: 0; padding: 0; }
  html, body {
    width: 1200px; height: 902px; overflow: hidden;
    background: var(--page);
    font-family: "PT Sans", Tahoma, sans-serif;
  }
  .stage { position: relative; width: 1200px; height: 902px; }
  .card {
    position: absolute; top: 306px;
    width: 500px; height: 290px;
    border-radius: 24px; overflow: hidden;
  }
  .card--back { left: 70px; background: var(--card-black); }
  .card--front { left: 630px; background: var(--card-white); }

  .brand { position: absolute; line-height: 1; }
  .brand__name { font-weight: 700; font-size: 40px; color: var(--brand-blue); letter-spacing: -0.5px; }
  .brand__tag { font-size: 17px; color: var(--tag-grey); letter-spacing: 5px; margin-top: 4px; padding-left: 4px; }
  .card--back .brand { left: 0; right: 0; top: 98px; text-align: center; }
  .card--back .brand__name { color: #3550b0; }
  .card--back .brand__tag { color: #8a8a8a; }
  .back-url {
    position: absolute; left: 0; right: 0; top: 196px;
    text-align: center; font-size: 16px; color: var(--url-grey); letter-spacing: 0.5px;
  }

  .card--front .brand { left: 26px; top: 118px; }
  .card--front .brand__name { font-size: 34px; }
  .card--front .brand__tag { font-size: 15px; letter-spacing: 4px; }

  .panel {
    position: absolute; left: 232px; top: 0; width: 248px; height: 290px;
    background: var(--panel-blue);
  }
  .panel__notch { position: absolute; left: -12px; top: 68px; }
  .person { position: absolute; left: 22px; top: 40px; color: var(--text-light); }
  .person__name { font-size: 22px; letter-spacing: 0.3px; }
  .person__title { font-size: 13px; margin-top: 3px; letter-spacing: 0.3px; }
  .contacts { position: absolute; left: 22px; top: 136px; list-style: none; color: var(--text-light); font-size: 11.5px; }
  .contacts li { display: flex; align-items: flex-start; gap: 9px; margin-bottom: 9px; line-height: 1.3; }
  .contacts svg { flex: none; margin-top: 1px; }
</style>
</head>
<body>
<main class="stage">
  <section class="card card--back" aria-label="Card back">
    <div class="brand">
      <div class="brand__name">Threadline</div>
      <div class="brand__tag">Legal Tech</div>
    </div>
    <div class="back-url">www.threadline.net</div>
  </section>

  <section class="card card--front" aria-label="Card front">
    <div class="brand">
      <div class="brand__name">Threadline</div>
      <div class="brand__tag">Legal Tech</div>
    </div>
    <div class="panel">
      <svg class="panel__notch" width="12" height="22" viewBox="0 0 12 22"><polygon points="12,0 0,11 12,22" fill="var(--panel-blue)"/></svg>
      <div class="person">
        <div class="person__name">daniel m. porter jr.</div>
        <div class="person__title">president &amp; virtual cio</div>
      </div>
      <ul class="contacts">
        <li>
          <svg width="11" height="13" viewBox="0 0 11 13"><path d="M5.5 0a4.5 4.5 0 0 0-4.5 4.5C1 8 5.5 13 5.5 13S10 8 10 4.5A4.5 4.5 0 0 0 5.5 0z" fill="#fff"/><circle cx="5.5" cy="4.5" r="1.6" fill="var(--panel-blue)"/></svg>
          <span>4817 Marlowe Hatchfield Rd.<br>Suite 518 Cincinnati, OH 45917</span>
        </li>
        <li>
          <svg width="11" height="11" viewBox="0 0 24 24"><path d="M6.6 10.8a15 15 0 0 0 6.6 6.6l2.2-2.2a1 1 0 0 1 1-.25 11.4 11.4 0 0 0 3.6.57 1 1 0 0 1 1 1V20a1 1 0 0 1-1 1A17 17 0 0 1 3 4a1 1 0 0 1 1-1h3.5a1 1 0 0 1 1 1c0 1.25.2 2.45.57 3.57a1 1 0 0 1-.25 1z" fill="#fff"/></svg>
          <span>513.555.0148</span>
        </li>
        <li>
          <svg width="12" height="10" viewBox="0 0 12 10"><rect x="0.5" y="0.5" width="11" height="9" fill="#fff"/><polyline points="0.8,1 6,5.5 11.2,1" fill="none" stroke="var(--panel-blue)" stroke-width="1.2"/></svg>
          <span>dporter@threadline.net</span>
        </li>
        <li>
          <svg width="12" height="12" viewBox="0 0 12 12"><circle cx="6" cy="6" r="5.3" fill="#fff"/><g fill="none" stroke="var(--panel-blue)" stroke-width="0.8"><ellipse cx="6" cy="6" rx="2.3" ry="5.3"/><line x1="0.7" y1="6" x2="11.3" y2="6"/><line x1="1.5" y1="3.3" x2="10.5" y2="3.3"/><line x1="1.5" y1="8.7" x2="10.5" y2="8.7"/></g></svg>
          <span>www.threadline.net</span>
        </li>
      </ul>
    </div>
  </section>
</main>
</body>
</html>
```